Calvanto Group Real Estate Company business cards

New business card design, we are generally happy with the basic layout of the existing front of business card, (feel free to change) but require a head shot photo on the back side.

http://www.calvanto.com.au/

Attached logos, and existing business card

------------------------------

Target Market(s)

Real estate

Industry/Entity Type

Real Estate

Contact Information for Business Card

Standard size double sided

Font styles to use
Other font styles liked:
• Futura

Requirements
Must have
• Photo head shot on the back side
Nice to have
• yes
Should not have
• No

```html
<!DOCTYPE html>
<html lang="en">
<head>
<meta charset="utf-8">
<title>Calvanto Group – Business Cards</title>
<link rel="stylesheet" href="https://fonts.googleapis.com/css2?family=Jost:wght@400;500;600&display=swap">
<style>
  :root {
    --backdrop: #2b2b2b;
    --card: #ffffff;
    --navy: #2b1f5e;
    --orange: #f5901e;
    --ink: #1d1d24;
    --photo-top: #e9e6ea;
    --photo-suit: #2f3f6b;
  }
  * { box-sizing: border-box; margin: 0; padding: 0; }
  html, body { width: 1200px; height: 1054px; overflow: hidden; }
  body {
    background: var(--backdrop);
    font-family: "Jost", sans-serif;
    display: flex;
    flex-direction: column;
    align-items: center;
    justify-content: center;
    gap: 36px;
  }
  .card {
    position: relative;
    width: 820px;
    height: 469px;
    background: var(--card);
    overflow: hidden;
  }
  .wordmark {
    font-family: "Jost", sans-serif;
    font-weight: 500;
    color: var(--navy);
    letter-spacing: 0.5px;
    white-space: nowrap;
    line-height: 1;
  }

  /* Front */
  .card-front .headshot {
    position: absolute;
    right: 0;
    top: 0;
    width: 290px;
    height: 320px;
    background: linear-gradient(180deg, var(--photo-top) 0%, #d9c3ae 35%, var(--photo-suit) 70%, #27345a 100%);
    -webkit-mask-image: linear-gradient(90deg, transparent 0%, #000 30%);
    mask-image: linear-gradient(90deg, transparent 0%, #000 30%);
  }
  .card-front .wordmark {
    position: absolute;
    left: 90px;
    top: 200px;
    font-size: 48px;
  }
  .card-front .tagline {
    position: absolute;
    left: 170px;
    top: 285px;
    font-size: 16px;
    font-weight: 600;
    color: var(--ink);
    letter-spacing: 1px;
  }

  /* Back */
  .rule-orange {
    position: absolute;
    left: 40px;
    top: 105px;
    width: 540px;
    height: 3px;
    background: var(--orange);
  }
  .rule-navy {
    position: absolute;
    left: 330px;
    top: 412px;
    width: 470px;
    height: 3px;
    background: var(--navy);
  }
  .card-back .wordmark {
    position: absolute;
    right: 26px;
    top: 36px;
    font-size: 46px;
    writing-mode: vertical-rl;
  }
  .contact {
    position: absolute;
    left: 90px;
    top: 228px;
    color: var(--ink);
  }
  .contact .name {
    font-size: 22px;
    font-weight: 600;
    color: var(--navy);
    line-height: 1.1;
  }
  .contact .role {
    font-size: 18px;
    margin-bottom: 10px;
  }
  .contact .line {
    display: flex;
    align-items: center;
    gap: 10px;
    font-size: 21px;
    line-height: 1.3;
  }
  .contact .line svg { width: 16px; height: 16px; flex: none; }
  .contact .company {
    margin-top: 14px;
    font-size: 21px;
    line-height: 1.3;
  }
</style>
</head>
<body>

  <section class="card card-front">
    <div class="headshot" role="img" aria-label="Head shot photo of the agent in a navy suit and blue tie"></div>
    <div class="wordmark">Calvanto Group</div>
    <div class="tagline">BUY &nbsp;|&nbsp; SELL &nbsp;|&nbsp; RENT</div>
  </section>

  <section class="card card-back">
    <div class="rule-orange"></div>
    <div class="rule-navy"></div>
    <div class="wordmark">Calvanto Group</div>
    <div class="contact">
      <div class="name">Daniel Tran</div>
      <div class="role">Director</div>
      <div class="line">
        <svg viewBox="0 0 16 16" aria-hidden="true"><rect x="4" y="1" width="8" height="14" rx="1.5" fill="none" stroke="var(--navy)" stroke-width="1.6"/><line x1="7" y1="12.5" x2="9" y2="12.5" stroke="var(--navy)" stroke-width="1.4"/></svg>
        0412 555 308
      </div>
      <div class="line">
        <svg viewBox="0 0 16 16" aria-hidden="true"><rect x="1" y="3" width="14" height="10" fill="var(--navy)"/><polyline points="1,3 8,9 15,3" fill="none" stroke="#fff" stroke-width="1.2"/></svg>
        daniel.tran@calvanto.com.au
      </div>
      <div class="line">
        <svg viewBox="0 0 16 16" aria-hidden="true"><circle cx="8" cy="8" r="7" fill="var(--navy)"/><ellipse cx="8" cy="8" rx="3" ry="7" fill="none" stroke="#fff" stroke-width="0.9"/><line x1="1" y1="8" x2="15" y2="8" stroke="#fff" stroke-width="0.9"/></svg>
        www.calvanto.com.au
      </div>
      <div class="company">Calvanto Group<br>ABN: 41 208 663 917</div>
    </div>
  </section>

</body>
</html>
```